Modern Attractive Letterhead for Veterinary House Call Business.

A letterhead which can be printed on A4, A5 and A6 paper sizes.
To have: ( our files to be uploaded)
1. Logo with Text
2. telephone
3. email
4. website
5. Address

Target Market(s)

60-85year mainly women pet owners. Also market include families, young professionals, busy people who have dogs and cats

Industry/Entity Type

Business

Requirements
Must have
• 1. Logo with Text ( provided)
• 2. telephone
• 3. email
• 4. website
• 5. Address
Nice to have
• Needs to be modern, preferably warm and caring in nature( if possible )
Should not have
• difficulty in printing A5 and A6

```html
<!DOCTYPE html>
<html lang="en">
<head>
<meta charset="utf-8">
<title>Kind Paw Visits – Letterhead</title>
<link rel="stylesheet" href="https://fonts.googleapis.com/css2?family=Cinzel:wght@400;600&display=swap">
<style>
  :root {
    --paper: #fbfbfc;
    --ink: #3b3b3d;
    --rule: #9a9a9a;
    --brand-blue: #2b55a3;
    --green-dark: #1c8a3e;
    --green-light: #86c240;
    --blue-light: #2aa8e0;
    --blue-dark: #2b3a8c;
    --icon-green: #3f9a3a;
  }
  * { margin: 0; padding: 0; box-sizing: border-box; }
  html, body { width: 948px; height: 1200px; overflow: hidden; }
  body { background: var(--paper); font-family: "Cinzel", serif; color: var(--ink); }
  .letterhead {
    position: relative;
    width: 948px;
    height: 1200px;
    background: linear-gradient(160deg, #ffffff 0%, #f9fafb 55%, #f1f2f5 100%);
    overflow: hidden;
  }
  .brand {
    position: absolute;
    left: 48px;
    top: 70px;
    display: flex;
    align-items: center;
    gap: 14px;
  }
  .brand-mark {
    width: 22px;
    height: 22px;
    background: var(--brand-blue);
  }
  .brand-name {
    font-family: "Cinzel", serif;
    font-weight: 600;
    font-size: 40px;
    letter-spacing: 1px;
    color: var(--brand-blue);
    line-height: 1;
  }
  .contact {
    position: absolute;
    left: 668px;
    top: 30px;
    padding-left: 13px;
    border-left: 1px solid var(--rule);
    font-style: normal;
    font-size: 13.5px;
    line-height: 20px;
    color: var(--ink);
    white-space: nowrap;
  }
  .contact-line { display: flex; align-items: center; gap: 6px; }
  .contact-line svg { width: 12px; height: 12px; flex: none; }
  .contact-address { margin-top: 10px; line-height: 17px; }
  .footer-band { position: absolute; left: 0; top: 1160px; width: 948px; height: 40px; }
  .website {
    position: absolute;
    right: 30px;
    top: 1169px;
    font-size: 17px;
    letter-spacing: 3px;
    color: #ffffff;
    line-height: 22px;
  }
</style>
</head>
<body>
  <div class="letterhead">
    <header class="brand">
      <span class="brand-mark"></span>
      <span class="brand-name">Kind Paw Visits</span>
    </header>

    <address class="contact">
      <div class="contact-line">
        <svg viewBox="0 0 16 16" aria-hidden="true"><path fill="none" stroke="var(--icon-green)" stroke-width="1.8" d="M4 2 L6.5 5 L5 7 Q6.5 10 9 11 L11 9.5 L14 12 L12.5 14 Q5 13.5 2 4 Z"/></svg>
        <span>0400 555 218</span>
      </div>
      <div class="contact-line">
        <svg viewBox="0 0 16 16" aria-hidden="true"><rect x="1.5" y="4" width="13" height="9" rx="1" fill="var(--icon-green)"/><path d="M1.5 4.5 L8 9.5 L14.5 4.5" fill="none" stroke="#fff" stroke-width="1.4"/></svg>
        <span>HELLO@KINDPAWVISITS.COM.AU</span>
      </div>
      <div class="contact-address">PO Box 4410 Brookfield Vale<br>QLD 4000</div>
    </address>

    <svg class="footer-band" viewBox="0 0 948 40" aria-hidden="true">
      <defs>
        <linearGradient id="band-green" x1="0" x2="1" y1="0" y2="0">
          <stop offset="0" stop-color="var(--green-dark)"/>
          <stop offset="1" stop-color="var(--green-light)"/>
        </linearGradient>
        <linearGradient id="band-blue" x1="0" x2="1" y1="0" y2="0">
          <stop offset="0" stop-color="var(--blue-light)"/>
          <stop offset="1" stop-color="var(--blue-dark)"/>
        </linearGradient>
      </defs>
      <polygon points="0,20 512,20 492,40 0,40" fill="url(#band-green)"/>
      <polygon points="536,0 948,0 948,40 502,40" fill="url(#band-blue)"/>
    </svg>
    <div class="website">WWW.KINDPAWVISITS.COM.AU</div>
  </div>
</body>
</html>
```